Granite Tile Retail Website

We need wireframe PSD for a website selling granite tile. There are 4 custom pages, shopping cart page, and checkout page. I have a logo designed but the color scheme is up to you.
Color Gallery - We have approximately 20 different stone colors. Each color will have a little gallery of its own pictures. On this page the customer can also add a sample piece of the color they are viewing to their shopping cart.
Questions Page - This page has 3 elements
1. Upload or fax diagram of kitchen for quotation
2. Installation video
3. Installation FAQ (text)
Order Page - This page has 3 steps for the customer
1. Customer chooses his color.
2. For each color we have numerous different products. He inputs the quantity of each product.
3. Customer is given total price and shipping quote. If order over $500 it says "This order qualifies for free shipping". Customer can click on button to "Order Now"
Shopping Cart - Very standard, just like I have attached here. Just modify for your colors / font.
Checkout - Just like in the attached. See design-explanation.docx for minor adjustments.
I have vector file for logo.
Updates
Please try to post your designs by tonightÂ
Target Market(s)
Home owners 40-60 years old
Industry/Entity Type
Shopping
Look and feel

```html
<!DOCTYPE html>
<html lang="en">
<head>
<meta charset="utf-8">
<title>Stonecrest Granite — Home</title>
<link href="https://fonts.googleapis.com/css2?family=Bebas+Neue&family=Noto+Sans:wght@400&display=swap" rel="stylesheet">
<style>
  :root {
    --page-bg: #ececec;
    --card-bg: #ffffff;
    --card-edge: #dedede;
    --rule: #dcdcdc;
    --gold: #f0b95a;
    --gold-light: #f4ca80;
    --gold-dark: #dc9e36;
    --gold-edge: #c98a25;
    --ink: #2b2b2b;
    --nav-ink: #3a3a3a;
    --maroon: #4a1d2b;
    --body-ink: #3c3c3c;
    --hero-frame: #0c0c0c;
    --hero-panel-top: #3a3a3a;
    --hero-panel-bottom: #0d0d0d;
    --hero-text: #f2f2f2;
    --footer-top: #ececec;
    --footer-bottom: #fdfdfd;
    --badge-seal: #c9b43a;
    --badge-blue: #1f6a8e;
    --badge-navy: #203f78;
  }
  * { margin: 0; padding: 0; box-sizing: border-box; }
  html, body { width: 1200px; height: 1000px; overflow: hidden; }
  body { background: var(--page-bg); font-family: "Noto Sans", sans-serif; position: relative; }

  .site { position: absolute; left: 44px; top: 42px; width: 1112px; height: 921px;
          background: var(--card-bg); border: 1px solid var(--card-edge); }

  .rule { position: absolute; left: 22px; width: 1067px; height: 1px; background: var(--rule); }
  .rule--top { top: 28px; }
  .rule--header { top: 162px; }

  .brand { position: absolute; left: 56px; top: 62px; display: flex; align-items: center; gap: 12px;
           font-family: "Bebas Neue", sans-serif; font-size: 50px; line-height: 1; color: var(--maroon);
           letter-spacing: 2px; }
  .brand__mark { width: 38px; height: 38px; background: var(--gold); }

  .main-nav { position: absolute; right: 33px; top: 64px; height: 64px; display: flex; }
  .main-nav a { font-family: "Bebas Neue", sans-serif; font-size: 27px; color: var(--nav-ink);
                text-decoration: none; padding: 0 11px; display: flex; align-items: center;
                border-left: 1px solid #555; }
  .main-nav a:first-child { border-left: none; }
  .main-nav a.is-current { color: var(--gold); }

  .hero { position: absolute; left: 22px; top: 182px; width: 1066px; height: 331px;
          background: var(--hero-frame); padding: 5px; display: flex; }
  .hero__media { position: relative; width: 570px; height: 321px;
                 background: linear-gradient(160deg, #8e6e4c 0%, #c8a378 40%, #e6cf9f 70%, #9c7a55 100%); }
  .hero__play { position: absolute; left: 263px; top: 140px; }
  .hero__copy { flex: 1; height: 321px; padding: 48px 24px 0 26px;
                background: linear-gradient(180deg, var(--hero-panel-top), var(--hero-panel-bottom)); }
  .hero__title { font-family: "Bebas Neue", sans-serif; font-weight: 400; font-size: 48px; line-height: 1;
                 color: var(--gold); }
  .hero__text { margin-top: 36px; font-size: 17.5px; line-height: 28px; color: var(--hero-text);
                text-align: justify; }
  .hero__text p { text-indent: 40px; }
  .hero__more { color: var(--gold); font-weight: bold; margin-left: 10px; }

  .actions { position: absolute; left: 23px; top: 532px; display: flex; gap: 3px; }
  .action { width: 352px; height: 84px; display: flex; align-items: center; gap: 16px; padding-left: 16px;
            background: linear-gradient(180deg, var(--gold-light), var(--gold-dark));
            border: 2px solid var(--gold-edge); font-family: "Bebas Neue", sans-serif; font-size: 50px;
            color: var(--ink); line-height: 1; padding-top: 4px; }
  .action svg { flex: none; margin-top: -4px; }

  .intro { position: absolute; left: 45px; top: 638px; width: 1022px; font-size: 14.4px;
           line-height: 21.5px; color: var(--body-ink); text-align: justify; }
  .intro p { text-indent: 40px; }

  .site-footer { position: absolute; left: 22px; top: 780px; width: 1067px; height: 139px;
                 border-top: 1px solid var(--rule);
                 background: linear-gradient(180deg, var(--footer-top), var(--footer-bottom)); }
  .footer-links { position: absolute; top: 18px; list-style: none; }
  .footer-links li { font-family: "Bebas Neue", sans-serif; font-size: 18px; line-height: 21px; color: var(--maroon); }
  .footer-links li.is-current { color: var(--gold); }
  .footer-links--site { left: 35px; }
  .footer-links--policy { left: 272px; }
  .footer-links--more { left: 534px; }

  .trust { position: absolute; left: 812px; top: 22px; width: 220px; height: 105px; }
  .trust__seal { position: absolute; left: 0; top: 1px; width: 84px; height: 66px; border-radius: 50%;
                 background: var(--badge-seal); }
  .trust__accredited { position: absolute; left: 92px; top: 0; width: 129px; height: 49px;
                       border-radius: 5px; background: var(--badge-blue); }
  .trust__pay { position: absolute; left: 92px; top: 58px; width: 129px; height: 44px;
                border-radius: 5px; background: var(--badge-navy); }
</style>
</head>
<body>
  <div class="site">
    <div class="rule rule--top"></div>

    <header>
      <div class="brand"><span class="brand__mark"></span>Stonecrest Granite</div>
      <nav class="main-nav">
        <a class="is-current" href="#">Home</a>
        <a href="#">Gallery</a>
        <a href="#">Questions</a>
        <a href="#">Order</a>
        <a href="#">Shopping Cart</a>
      </nav>
    </header>

    <div class="rule rule--header"></div>

    <section class="hero">
      <div class="hero__media" role="img" aria-label="Installation video: kitchen with granite countertops and wooden cabinets">
        <svg class="hero__play" width="48" height="48" viewBox="0 0 48 48" aria-hidden="true">
          <circle cx="24" cy="24" r="22" fill="#3a3a3a" fill-opacity=".8" stroke="#dddddd" stroke-width="2"/>
          <path d="M19 14 L34 24 L19 34 Z" fill="#eeeeee"/>
        </svg>
      </div>
      <div class="hero__copy">
        <h1 class="hero__title">Welcome to our site</h1>
        <div class="hero__text">
          <p>Donec quam felis, ultricies nec, pellentesque eu, pretium quis, sem. Nulla consequat massa quis enim. Donec pede justo, fringilla vel, aliquet nec, vulputate eget, arcu. In enim justo, rhoncus ut, imperdiet a, venenatis vitae, justo.</p>
          <p>Nullam dictum felis eu pede mollis <span class="hero__more">»</span></p>
        </div>
      </div>
    </section>

    <div class="actions">
      <a class="action">
        <svg width="50" height="50" viewBox="0 0 50 50" aria-hidden="true">
          <circle cx="25" cy="25" r="23" fill="#2d2d2d"/>
          <path d="M18 19 a7 7 0 1 1 10 6 c-2 1 -3 2 -3 5" fill="none" stroke="#f2f2f2" stroke-width="4" stroke-linecap="round"/>
          <circle cx="25" cy="37" r="2.6" fill="#f2f2f2"/>
        </svg>
        Questions?
      </a>
      <a class="action">
        <svg width="50" height="50" viewBox="0 0 50 50" aria-hidden="true">
          <path d="M25 4 C10 4 3 15 3 25 C3 37 13 46 24 46 C29 46 30 42 28 39 C26 36 28 33 32 33 L38 33 C44 33 47 29 47 24 C47 12 37 4 25 4 Z" fill="#2d2d2d"/>
          <circle cx="14" cy="20" r="4" fill="#f2f2f2"/>
          <circle cx="24" cy="13" r="4" fill="#f2f2f2"/>
          <circle cx="13" cy="32" r="4" fill="#f2f2f2"/>
          <path d="M46 8 L30 28" stroke="#f2f2f2" stroke-width="4" stroke-linecap="round"/>
        </svg>
        Color Scheme
      </a>
      <a class="action">
        <svg width="50" height="50" viewBox="0 0 50 50" aria-hidden="true">
          <rect x="3" y="5" width="40" height="40" rx="3" fill="#2d2d2d"/>
          <path d="M14 36 L16 28 L36 8 L42 14 L22 34 Z" fill="#f2f2f2" stroke="#2d2d2d" stroke-width="2"/>
        </svg>
        Get a Quote
      </a>
    </div>

    <section class="intro">
      <p>Lorem ipsum dolor sit amet, consectetuer adipiscing elit. Aenean commodo ligula eget dolor. Aenean massa. Cum sociis natoque penatibus et magnis dis parturient montes, nascetur ridiculus mus. Donec quam felis, ultricies nec, pellentesque eu, pretium quis, sem. Nulla consequat massa quis enim. Donec pede justo, fringilla vel, aliquet nec, vulputate eget, arcu. In enim justo, rhoncus ut, imperdiet a, venenatis vitae, justo.</p>
      <p>Nullam dictum felis eu pede mollis pretium. Integer tincidunt. Cras dapibus. Vivamus elementum semper nisi. Donec quam felis, ultricies nec, pellentesque eu, pretium quis, sem. Nulla consequat massa quis enim.</p>
    </section>

    <footer class="site-footer">
      <ul class="footer-links footer-links--site">
        <li class="is-current">Home</li>
        <li>Gallery</li>
        <li>Questions</li>
        <li>Order</li>
        <li>Shopping Cart</li>
      </ul>
      <ul class="footer-links footer-links--policy">
        <li>Return Policy</li>
        <li>Shipping Policy</li>
        <li>Privacy</li>
        <li>Terms of Use</li>
        <li>Customer Service</li>
      </ul>
      <ul class="footer-links footer-links--more">
        <li>New Link</li>
        <li>Another Link</li>
        <li>Third Link</li>
        <li>Fourth Link</li>
        <li>Fifth Link</li>
      </ul>
      <div class="trust">
        <div class="trust__seal" role="img" aria-label="Verified merchant seal"></div>
        <div class="trust__accredited" role="img" aria-label="Accredited business badge"></div>
        <div class="trust__pay" role="img" aria-label="Secure payment badge"></div>
      </div>
    </footer>
  </div>
</body>
</html>
```